One of a kind service business!

We are the only ocean freight auditing company in the entire world that does what we do. We provide a innovative service in auditing our clients invoices for billing errors as it relates to the import and export of their products anywhere in the world. We'd like to retain the current logo - but we are open to any interesting concepts that can complete the card.

Target Market(s)

C-Level and Senior Financial executives

Industry/Entity Type

Auditing

Requirements
Must have

• ONE SIDED ONLY
Should not have
• no cartoonish images

```html
<!DOCTYPE html>
<html lang="en">
<head>
<meta charset="utf-8">
<title>Tidemark Review – Business Card</title>
<link rel="stylesheet" href="https://fonts.googleapis.com/css2?family=Noto+Sans:wght@400;700&display=swap">
<style>
  :root {
    --backdrop: #d9dcdf;
    --card: #ffffff;
    --ocean: #0a72a8;
    --lime: #b6da7c;
    --ink: #333a40;
    --icon: #1b6fa3;
    --light: #ffffff;
  }
  * { margin: 0; padding: 0; box-sizing: border-box; }
  html, body {
    width: 1200px; height: 944px; overflow: hidden;
    background: var(--backdrop);
    font-family: "Noto Sans", Arial, sans-serif;
  }
  .canvas { position: relative; width: 1200px; height: 944px; }
  .card {
    position: absolute; left: 110px; top: 196px;
    width: 980px; height: 553px;
    background: var(--card);
    border-radius: 28px;
    overflow: hidden;
    box-shadow: 0 10px 30px rgba(0,0,0,0.25);
  }
  .wave { position: absolute; inset: 0; width: 100%; height: 100%; }
  .brand {
    position: absolute; left: 48px; top: 82px;
    font-size: 50px; font-weight: 700; color: var(--ocean);
    line-height: 1; white-space: nowrap;
    display: flex; align-items: center; gap: 14px;
  }
  .brand-dot { width: 16px; height: 16px; border-radius: 50%; background: var(--lime); flex: none; }
  .contact { position: absolute; left: 70px; color: var(--ink); font-size: 25px; line-height: 32px; white-space: nowrap; }
  .contact-row { display: flex; align-items: center; }
  .contact-row svg { width: 21px; height: 21px; margin-right: 15px; flex: none; fill: var(--icon); }
  .address { top: 205px; }
  .address .contact-row { align-items: flex-start; }
  .address .contact-row svg { margin-top: 5px; }
  .address .lines { display: flex; flex-direction: column; }
  .channels { top: 318px; line-height: 33px; }
  .person {
    position: absolute; left: 620px; width: 330px; top: 444px;
    text-align: center; color: var(--light);
  }
  .person-name { font-size: 36px; line-height: 44px; }
  .person-title { font-size: 23px; line-height: 30px; }
</style>
</head>
<body>
<div class="canvas">
  <div class="card">
    <svg class="wave" viewBox="0 0 418 236" preserveAspectRatio="none" aria-hidden="true">
      <path fill="var(--lime)" d="M289,0 C250,45 262,115 236,165 C222,195 210,220 205,236 L418,236 L418,0 Z"/>
      <path fill="var(--ocean)" d="M306,0 C268,48 276,125 252,175 C240,200 230,222 224,236 L418,236 L418,0 Z"/>
    </svg>

    <div class="brand"><span>Tidemark Review</span><span class="brand-dot"></span></div>

    <div class="contact address">
      <div class="contact-row">
        <svg viewBox="0 0 24 24"><path d="M12 3 2 12h3v9h5v-6h4v6h5v-9h3z"/></svg>
        <div class="lines">
          <span>Riverside Business Park</span>
          <span>Lindova 12, Brno</span>
          <span>Czech Republic 60200</span>
        </div>
      </div>
    </div>

    <div class="contact channels">
      <div class="contact-row">
        <svg viewBox="0 0 24 24"><path d="M6.6 10.8a15 15 0 0 0 6.6 6.6l2.2-2.2c.3-.3.7-.4 1-.2 1.1.4 2.3.6 3.6.6.6 0 1 .4 1 1V20c0 .6-.4 1-1 1A17 17 0 0 1 3 4c0-.6.4-1 1-1h3.5c.6 0 1 .4 1 1 0 1.3.2 2.5.6 3.6.1.3 0 .7-.2 1z"/></svg>
        <span>+420 555 010 142</span>
      </div>
      <div class="contact-row">
        <svg viewBox="0 0 24 24"><path d="M8 1h8a2 2 0 0 1 2 2v18a2 2 0 0 1-2 2H8a2 2 0 0 1-2-2V3a2 2 0 0 1 2-2zm0 3v14h8V4zm4 15.5a1.2 1.2 0 1 0 0 2.4 1.2 1.2 0 0 0 0-2.4z"/></svg>
        <span>+420 555 020 058</span>
      </div>
      <div class="contact-row">
        <svg viewBox="0 0 24 24"><path d="M6.6 10.8a15 15 0 0 0 6.6 6.6l2.2-2.2c.3-.3.7-.4 1-.2 1.1.4 2.3.6 3.6.6.6 0 1 .4 1 1V20c0 .6-.4 1-1 1A17 17 0 0 1 3 4c0-.6.4-1 1-1h3.5c.6 0 1 .4 1 1 0 1.3.2 2.5.6 3.6.1.3 0 .7-.2 1z"/></svg>
        <span>+1 555 014 7905 - USA</span>
      </div>
      <div class="contact-row">
        <svg viewBox="0 0 24 24"><path d="M6 2h10v6H6zM3 9h18a1 1 0 0 1 1 1v8a1 1 0 0 1-1 1h-3v3H6v-3H3a1 1 0 0 1-1-1v-8a1 1 0 0 1 1-1zm5 7v4h8v-4z"/></svg>
        <span>+420 555 030 200</span>
      </div>
      <div class="contact-row">
        <svg viewBox="0 0 24 24"><path d="M12 2a10 10 0 1 0 0 20 10 10 0 0 0 0-20zm6.9 9h-3a15 15 0 0 0-1.3-6A8 8 0 0 1 18.9 11zM12 4.1c.9 1.2 1.7 3.6 1.9 6.9h-3.8c.2-3.3 1-5.7 1.9-6.9zM9.4 5a15 15 0 0 0-1.3 6h-3A8 8 0 0 1 9.4 5zm-4.3 8h3a15 15 0 0 0 1.3 6A8 8 0 0 1 5.1 13zm6.9 6.9c-.9-1.2-1.7-3.6-1.900-6.9h3.8c-.2 3.3-1 5.7-1.9 6.9zm2.6-.9a15 15 0 0 0 1.3-6h3a8 8 0 0 1-4.3 6z"/></svg>
        <span>www.tidemarkreview.net</span>
      </div>
      <div class="contact-row">
        <svg viewBox="0 0 24 24"><path d="M2 5h20v14H2zm2 2v.5l8 5.5 8-5.5V7zm0 3v7h16v-7l-8 5.5z"/></svg>
        <span>martink@tidemarkreview.net</span>
      </div>
    </div>

    <div class="person">
      <div class="person-name">Martin Kessler</div>
      <div class="person-title">CEO</div>
    </div>
  </div>
</div>
</body>
</html>
```